Lanterns Eve Festival 2021

We would like to design a campaign with a great picture of Desmond Alcott Fairweather, Jr. with a big tear coming out of his eye, that image with the Creed of the Harvest to the Lantern. With a caption under it that says: America, you are better than this.

```html
<!DOCTYPE html>
<html lang="en">
<head>
<meta charset="utf-8">
<title>Lanterns Eve Festival 2021 — America, You Are Better Than This</title>
<link rel="stylesheet" href="https://fonts.googleapis.com/css2?family=Alfa+Slab+One&family=Josefin+Sans:wght@300;400&family=Libre+Baskerville:wght@700&display=swap">
<style>
  :root {
    --ink: #000000;
    --paper: #ffffff;
    --smoke: #1c1c1c;
    --creed-grey: #4a4a4a;
    --alert-red: #e00000;
  }
  html, body {
    margin: 0;
    padding: 0;
    overflow: hidden;
    background: var(--ink);
  }
  .poster {
    position: relative;
    width: 848px;
    height: 1200px;
    overflow: hidden;
    background:
      radial-gradient(ellipse at 40% 30%, #262626 0%, #111 45%, var(--ink) 75%);
  }
  .flag-backdrop {
    position: absolute;
    left: 0;
    top: 0;
    width: 420px;
    height: 700px;
    background: radial-gradient(ellipse at 20% 40%, #2a2a2a 0%, #141414 55%, transparent 80%);
    opacity: 0.8;
  }
  .creed {
    position: absolute;
    left: 500px;
    top: 30px;
    margin: 0;
    font-family: "Libre Baskerville", "Times New Roman", serif;
    font-weight: 700;
    font-size: 50px;
    line-height: 60px;
    color: var(--creed-grey);
    text-shadow: 0 0 6px rgba(0,0,0,0.9), 0 0 2px #6a6a6a;
    filter: blur(0.6px);
    transform: rotate(-6deg);
    transform-origin: left top;
    white-space: pre;
  }
  .portrait {
    position: absolute;
    left: 187px;
    top: 85px;
    width: 492px;
    height: 610px;
    background:
      radial-gradient(ellipse at 48% 35%, #e6e6e6 0%, #bdbdbd 25%, #555 48%, #151515 70%, transparent 85%);
  }
  .headline {
    position: absolute;
    left: 0;
    top: 0;
    width: 848px;
    height: 1200px;
  }
  .headline-country {
    font-family: "Alfa Slab One", "Rockwell", serif;
    font-size: 124px;
    fill: var(--paper);
  }
  .headline-you-are {
    font-family: "Josefin Sans", "Futura", sans-serif;
    font-weight: 400;
    font-size: 118px;
    fill: var(--paper);
  }
  .headline-better {
    font-family: "Alfa Slab One", "Rockwell", serif;
    font-size: 114px;
  }
  .headline-better--white { fill: var(--paper); }
  .headline-better--red { fill: var(--alert-red); }
  .headline-than-this {
    font-family: "Josefin Sans", "Futura", sans-serif;
    font-weight: 300;
    font-size: 92px;
    fill: var(--paper);
  }
</style>
</head>
<body>
  <main class="poster">
    <div class="flag-backdrop" role="img" aria-label="Faint waving flag with stars in dark grey behind the portrait"></div>

    <p class="creed" aria-label="Creed of the Harvest to the Lantern">harvest
of the
of Lanterns
fellowship
it shines,
under stars
with warmth
for all.”</p>

    <div class="portrait" role="img" aria-label="High-contrast black and white portrait of Desmond Alcott Fairweather, Jr., hands folded under his chin, a single large tear falling from his eye"></div>

    <svg class="headline" viewBox="0 0 848 1200" aria-label="America, you are better than this">
      <defs>
        <clipPath id="better-lower">
          <polygon points="100,998 700,1042 700,1060 100,1060"/>
        </clipPath>
      </defs>
      <text class="headline-country" x="90" y="791" textLength="667" lengthAdjust="spacingAndGlyphs">AMERICA</text>
      <text class="headline-you-are" x="186" y="916" textLength="495" lengthAdjust="spacingAndGlyphs">YOU ARE</text>
      <text class="headline-better headline-better--white" x="110" y="1040" textLength="627" lengthAdjust="spacingAndGlyphs">BETTER</text>
      <text class="headline-better headline-better--red" x="110" y="1040" textLength="627" lengthAdjust="spacingAndGlyphs" clip-path="url(#better-lower)" aria-hidden="true">BETTER</text>
      <text class="headline-than-this" x="152" y="1142" textLength="543" lengthAdjust="spacing">THAN THIS</text>
    </svg>
  </main>
</body>
</html>
```